Letter head / email signature/ contract document templates

We need a professional email signature and letterhead designed for our established carpentry and maintenance company. Our Logo (attached) was originally designed 6 years ago by design guru and we love it, looking for something to compliment it ( not a home job)

```html
<!DOCTYPE html>
<html lang="en">
<head>
<meta charset="utf-8">
<title>Keystone Repair Co. — Stationery</title>
<link href="https://fonts.googleapis.com/css2?family=Lato:wght@400;700;900&family=Arimo:wght@400&display=swap" rel="stylesheet">
<style>
:root{
  --backdrop:#8a898b;
  --paper:#f1f1f2;
  --ink:#4a4a4c;
  --ink-dark:#333335;
  --brand-red:#c8141e;
  --band-light:#6b6b6d;
  --band-dark:#3a3a3c;
}
*{margin:0;padding:0;box-sizing:border-box}
html,body{width:1200px;height:858px;overflow:hidden;background:var(--backdrop)}
body{position:relative;font-family:'Lato',sans-serif;color:var(--ink)}
.sheet{position:absolute;background:var(--paper);overflow:hidden}
.letterhead{left:90px;top:72px;width:508px;height:714px}
.card-vertical{left:631px;top:216px;width:190px;height:257px}
.card-wide{left:631px;top:502px;width:403px;height:148px}
.signature-strip{left:630px;top:678px;width:515px;height:108px}
.abs{position:absolute}
.brand-name{position:absolute;display:flex;align-items:center;gap:5px;font-family:'Lato',sans-serif;font-weight:900;color:var(--ink-dark);white-space:nowrap;line-height:1}
.brand-name .mark{display:inline-block;background:var(--brand-red)}
.divider{position:absolute;width:1px;background:var(--ink)}
.info{position:absolute;line-height:1.2;white-space:nowrap}
.info .company{color:var(--brand-red)}
.contact{display:flex;align-items:center;gap:5px}
.contact svg{flex:none;fill:var(--brand-red)}
.person-name{color:var(--brand-red);font-weight:700;white-space:nowrap;line-height:1.1}
.person-role{white-space:nowrap;line-height:1.1}
.footer-bands{position:absolute;left:0;right:0;bottom:0}
.footer-bands .rule{height:3px;background:var(--band-light)}
.footer-bands .gap{height:2px;background:#fff}
.footer-bands .mid{background:var(--band-light)}
.footer-bands .base{background:var(--band-dark)}
.letter-body{position:absolute;left:38px;top:186px;width:432px;font-family:'Arimo',sans-serif;color:var(--ink)}
.salutation{font-size:12.7px;margin-bottom:24px}
.letter-body p{font-size:7.4px;line-height:10.8px;text-align:justify;margin-bottom:10.8px}
.closing{margin-top:16px}
.signature-area{position:absolute;left:35px;top:480px;width:147px;height:40px;background:linear-gradient(90deg,#e4e4e6,#d8d8da)}
</style>
</head>
<body>

<section class="sheet letterhead">
  <div class="brand-name" style="left:35px;top:64px;font-size:13px"><span class="mark" style="width:8px;height:8px"></span>Keystone Repair Co.</div>
  <div class="divider" style="left:167px;top:60px;height:33px"></div>
  <div class="info" style="left:187px;top:62px;font-size:8.5px">
    <div class="company">Keystone Repair Co.</div>
    <div>412 Cedar Hollow Road</div>
    <div>Juneau, Alaska 34521</div>
  </div>
  <div class="divider" style="left:324px;top:60px;height:33px"></div>
  <div class="info" style="left:345px;top:62px;font-size:8.5px">
    <div class="contact"><svg width="7" height="7" viewBox="0 0 10 10"><path d="M2 0l2 2.5-1 1.3c.6 1.3 1.6 2.3 2.9 2.9L7 5.7 9.5 8 8 10C4 9.5.5 6 0 2z"/></svg>369-555-0142</div>
    <div class="contact"><svg width="7" height="7" viewBox="0 0 10 10"><path d="M2 0h6v10H2zM3.2 1.2v7.6h3.6V1.2z"/></svg>369-555-0187</div>
    <div class="contact"><svg width="7" height="7" viewBox="0 0 10 10"><path d="M0 2h10v6H0zm1 1l4 3 4-3z"/></svg>info@keystonerepair.com</div>
  </div>

  <div class="letter-body">
    <div class="salutation">Dear Mr. Reyes,</div>
    <p>Lorem ipsum dolor sit amet, consectetur adipiscing elit. Donec orci purus, luctus vitae dignissim eu, iaculis sed purus. Vivamus faucibus, ipsum nec aliquet viverra, leo mauris condimentum ligula, sit amet sagittis enim ligula quis arcu. Nam egestas tortor id nisi porttitor mattis. In tortor ante, ultricies in suscipit a, tempus non massa. Vivamus et auctor mi. Fusce vel massa nulla. Phasellus nec eros mauris, et scelerisque orci.</p>
    <p>Donec malesuada orci vitae nulla accumsan porta a id massa. Quisque accumsan iaculis magna sit amet fringilla. Maecenas consequat, magna eget tincidunt semper, odio nibh rutrum mi, id feugiat ante nisi eu risus. Vestibulum nunc orci, rhoncus a placerat in, ultricies in mi. Cras mattis varius eros, vel fringilla nisi suscipit eget. Quisque scelerisque sagittis nulla at porttitor.</p>
    <p>Sed id augue vitae urna euismod commodo aliquet a quam. Pellentesque arcu velit, cursus et malesuada ut, consequat et diam. Nullam erat sem, rhoncus id ullamcorper vitae, rhoncus et arcu. In ultricies ultricies nulla, ut rutrum nisi iaculis at. Donec eu magna a metus ornare faucibus. Fusce aliquet faucibus ultricies. Morbi semper, est id tincidunt gravida, sem arcu adipiscing lacus, ac bibendum nulla leo eu purus. Quisque nec diam sed risus consectetur a ccumsan quis quis nibh. Vestibulum id purus lorem.</p>
    <p>It is a long established fact that a reader will be distracted by the readable content of a page when looking at its layout. The point of using Lorem Ipsum is that it has a more-or-less normal distribution of letters, as opposed to using 'Content here, content here', making it look like readable English. Many desktop publishing packages</p>
    <p>ada ut, consequat et diam. Nullam erat sem, rhoncus id ullamcorper vitae, rhoncus et arcu. In ultricies ultricies nulla, ut rutrum nisi iaculis at. Donec eu magna a metus ornare faucibus. Fusce aliquet faucibus ultricies. Morbi semper,</p>
    <p class="closing">Sincerely,</p>
  </div>
  <div class="signature-area" role="img" aria-label="Handwritten signature of the sender"></div>

  <div class="footer-bands"><div class="rule"></div><div class="gap"></div><div class="mid" style="height:5px"></div><div class="base" style="height:5px"></div></div>
</section>

<section class="sheet card-vertical">
  <div class="brand-name" style="left:24px;top:60px;font-size:13.5px"><span class="mark" style="width:8px;height:8px"></span>Keystone Repair Co.</div>
  <div class="abs" style="left:24px;top:114px">
    <div class="person-name" style="font-size:13.7px">Daniel Reyes</div>
    <div class="person-role" style="font-size:9.3px">President</div>
  </div>
  <div class="info" style="left:24px;top:160px;font-size:9px">
    <div class="contact" style="align-items:flex-start"><svg width="7" height="9" viewBox="0 0 8 10"><path d="M4 0a4 4 0 0 1 4 4c0 2.5-4 6-4 6S0 6.5 0 4a4 4 0 0 1 4-4zm0 2.3a1.7 1.7 0 1 0 0 3.4 1.7 1.7 0 0 0 0-3.4z"/></svg><div>412 Cedar Hollow Road<br>Juneau, Alaska 34521</div></div>
    <div style="height:4px"></div>
    <div class="contact"><svg width="7" height="7" viewBox="0 0 10 10"><path d="M2 0l2 2.5-1 1.3c.6 1.3 1.6 2.3 2.9 2.9L7 5.7 9.5 8 8 10C4 9.5.5 6 0 2z"/></svg>369-555-0142</div>
    <div class="contact"><svg width="7" height="7" viewBox="0 0 10 10"><path d="M2 0h6v10H2zM3.2 1.2v7.6h3.6V1.2z"/></svg>369-555-0187</div>
    <div class="contact"><svg width="7" height="7" viewBox="0 0 10 10"><path d="M0 2h10v6H0zm1 1l4 3 4-3z"/></svg>info@keystonerepair.com</div>
  </div>
  <div class="footer-bands"><div class="rule"></div><div class="gap"></div><div class="mid" style="height:5px"></div><div class="base" style="height:5px"></div></div>
</section>

<section class="sheet card-wide">
  <div class="brand-name" style="left:42px;top:66px;font-size:13.5px"><span class="mark" style="width:8px;height:8px"></span>Keystone Repair Co.</div>
  <div class="divider" style="left:195px;top:26px;height:90px"></div>
  <div class="abs" style="left:212px;top:23px">
    <div class="person-name" style="font-size:13.7px">Daniel Reyes</div>
    <div class="person-role" style="font-size:9.3px">President</div>
  </div>
  <div class="info" style="left:212px;top:57px;font-size:9px">
    <div>412 Cedar Hollow Road</div>
    <div>Juneau, Alaska 34521</div>
    <div style="height:5px"></div>
    <div class="contact"><svg width="7" height="7" viewBox="0 0 10 10"><path d="M2 0l2 2.5-1 1.3c.6 1.3 1.6 2.3 2.9 2.9L7 5.7 9.5 8 8 10C4 9.5.5 6 0 2z"/></svg>369-555-0142</div>
    <div class="contact"><svg width="7" height="7" viewBox="0 0 10 10"><path d="M2 0h6v10H2zM3.2 1.2v7.6h3.6V1.2z"/></svg>369-555-0187</div>
    <div class="contact"><svg width="7" height="7" viewBox="0 0 10 10"><path d="M0 2h10v6H0zm1 1l4 3 4-3z"/></svg>info@keystonerepair.com</div>
  </div>
  <div class="footer-bands"><div class="rule"></div><div class="gap"></div><div class="mid" style="height:5px"></div><div class="base" style="height:5px"></div></div>
</section>

<section class="sheet signature-strip">
  <div class="brand-name" style="left:36px;top:36px;font-size:13px"><span class="mark" style="width:8px;height:8px"></span>Keystone Repair Co.</div>
  <div class="divider" style="left:182px;top:26px;height:53px"></div>
  <div class="abs" style="left:209px;top:40px">
    <div class="person-name" style="font-size:13.7px">Daniel Reyes</div>
    <div class="person-role" style="font-size:9.3px">President</div>
  </div>
  <div class="divider" style="left:317px;top:26px;height:53px"></div>
  <div class="info" style="left:341px;top:21px;font-size:9px">
    <div class="contact" style="align-items:flex-start"><svg width="7" height="9" viewBox="0 0 8 10"><path d="M4 0a4 4 0 0 1 4 4c0 2.5-4 6-4 6S0 6.5 0 4a4 4 0 0 1 4-4zm0 2.3a1.7 1.7 0 1 0 0 3.4 1.7 1.7 0 0 0 0-3.4z"/></svg><div>412 Cedar Hollow Road<br>Juneau, Alaska 34521</div></div>
    <div style="height:3px"></div>
    <div class="contact"><svg width="7" height="7" viewBox="0 0 10 10"><path d="M2 0l2 2.5-1 1.3c.6 1.3 1.6 2.3 2.9 2.9L7 5.7 9.5 8 8 10C4 9.5.5 6 0 2z"/></svg>369-555-0142</div>
    <div class="contact"><svg width="7" height="7" viewBox="0 0 10 10"><path d="M2 0h6v10H2zM3.2 1.2v7.6h3.6V1.2z"/></svg>369-555-0187</div>
    <div class="contact"><svg width="7" height="7" viewBox="0 0 10 10"><path d="M0 2h10v6H0zm1 1l4 3 4-3z"/></svg>info@keystonerepair.com</div>
  </div>
  <div class="footer-bands"><div class="rule"></div><div class="gap"></div><div class="mid" style="height:5px"></div><div class="base" style="height:5px"></div></div>
</section>

</body>
</html>
```